School Website

I need a design for a School (2 sections: Primary 6-12 years and Secondary 12-18 years). The first page is just a choice of the 2 sections. After we'll need 2 websites (with the same structure: Menu, ...) but with different colors. In fact, we need for end of October, 6 design of school website. So the best websites are going to be made available to you in the future (in pixelharbor) but privately.

Target Market(s)

Public, Parents, ...

Coding

Coded - Design and coding required

Number of Pages Required

5+ page

Font styles to use
Sans Serif

Colors
34a6d7
85cae6
cee9f5
ffffff

Requirements
Must have
• You can check the old Website: http: / /velmot.be We need the same pages with the same content. Menu: - HomePage - News and communication (like blog page) - Activities (like blog page, with photo gallery) - Contact (Contact form + maps) - In the main menu, we need a special button to connect to an external Website ( button needs to be different than the other menu items The name of this button is "Parents Area"). The logo of 2 sections are attached. Please use it for the design and the choice of colors.
Nice to have
• This is a web design of other school that we like: https://www.quintelo.be

```html
<!DOCTYPE html>
<html lang="en">
<head>
<meta charset="utf-8">
<title>Lycée Royal de Velmont – Primary School</title>
<link href="https://fonts.googleapis.com/css2?family=Merriweather:wght@300;400;700;900&family=PT+Serif:wght@400;700&display=swap" rel="stylesheet">
<style>
:root{
  --blue:#0f67ad;
  --blue-deep:#0a4f88;
  --blue-soft:#8fbde3;
  --sky:#34a6d7;
  --ink:#1d1d1d;
  --muted:#444;
  --line:#8a8a8a;
  --white:#ffffff;
}
*{box-sizing:border-box;margin:0;padding:0}
html,body{width:1200px;height:3124px;overflow:hidden}
body{font-family:"PT Serif",serif;color:var(--ink);background:var(--white);position:relative}
.abs{position:absolute}

/* header */
.site-header{position:absolute;left:0;top:0;width:1200px;height:133px;background:var(--white)}
.brand{position:absolute;left:36px;top:30px;height:66px;width:322px;background:var(--blue);border-radius:8px;display:flex;align-items:center;gap:12px;padding:0 14px}
.brand-dot{width:40px;height:40px;border-radius:50%;background:var(--white);flex:none}
.brand-name{font-family:"Merriweather",serif;font-weight:700;font-size:19px;color:var(--white);white-space:nowrap}
.nav a{position:absolute;top:52px;font-size:18px;color:var(--ink);text-decoration:none;white-space:nowrap}
.nav .active{color:var(--blue);font-weight:700;border-bottom:1px solid var(--blue);padding-bottom:6px}
.nav .home-icon{position:absolute;left:436px;top:46px}
.btn-parents{position:absolute;left:1056px;top:48px;width:108px;height:30px;background:var(--blue);color:var(--white);font-size:13px;display:flex;align-items:center;justify-content:center}

/* hero */
.hero{position:absolute;left:0;top:133px;width:1200px;height:501px;background:linear-gradient(100deg,#3c4a58 0%,#6a6f6e 35%,#9a7d62 65%,#4a4f58 100%)}
.hero-shade{position:absolute;inset:0;background:linear-gradient(90deg,rgba(10,20,35,.55),rgba(10,20,35,.15))}
.hero-eyebrow{position:absolute;left:160px;top:112px;font-family:"Merriweather",serif;font-weight:300;font-size:34px;color:#c8dcef;letter-spacing:1px}
.hero-school{position:absolute;left:160px;top:160px;font-family:"Merriweather",serif;font-weight:300;font-size:44px;color:var(--sky)}
.hero-title{position:absolute;left:160px;top:220px;font-family:"Merriweather",serif;font-weight:900;font-size:33px;line-height:44px;color:var(--white);letter-spacing:1px}
.btn-enroll{position:absolute;left:159px;top:325px;width:184px;height:39px;border-radius:8px;background:var(--blue);color:var(--white);font-weight:700;font-size:16px;display:flex;align-items:center;justify-content:center}
.hero-arrow{position:absolute;top:230px}

/* info bar */
.info-bar{position:absolute;left:0;top:634px;width:1200px;height:104px;background:var(--blue);color:var(--white)}
.info-icon{position:absolute;top:24px;width:56px;height:56px;border-radius:50%;background:var(--white);display:flex;align-items:center;justify-content:center}
.info-label{position:absolute;top:20px;font-weight:700;font-size:15px}
.info-text{position:absolute;top:48px;font-size:15.5px;line-height:19px}

/* section heads */
.section-title{position:absolute;left:36px;font-family:"Merriweather",serif;font-weight:700;font-size:26px;border-left:3px solid var(--blue);padding-left:8px;line-height:22px}

/* blog cards */
.card{position:absolute;top:862px;height:487px;border:2px solid var(--line);background:var(--white)}
.card-head{height:53px;border-bottom:1px solid var(--line);display:flex;align-items:center;padding-left:22px;font-family:"Merriweather",serif;font-size:18px;font-weight:700}
.card-head span{border-left:3px solid var(--blue);padding-left:14px;line-height:18px}
.post{position:absolute;left:17px}
.thumb{position:absolute;left:0;top:0;width:95px;height:102px;background:linear-gradient(135deg,#d7b48f,#5e9bd4 60%,#e0574a)}
.date{position:absolute;left:0;top:0;width:54px;height:44px;background:var(--blue);color:var(--white);font-family:"Merriweather",serif;font-weight:700;font-size:16px;line-height:17px;text-align:center;padding-top:5px}
.post-text{position:absolute;left:110px;top:0;width:200px;font-size:15px;line-height:22px;color:var(--muted)}
.meta{display:flex;align-items:center;gap:8px;color:var(--blue);font-size:14px;margin-top:12px}
.notice{position:absolute;left:0;width:100%;border-bottom:1px solid var(--line);padding:14px 17px 0}
.notice p{font-size:15px;line-height:19px;color:var(--muted);text-align:justify}
.btn-view{position:absolute;left:17px;bottom:22px;width:271px;height:35px;background:var(--blue);color:var(--white);font-weight:700;font-size:14px;display:flex;align-items:center;justify-content:center}

/* activities */
.activities{position:absolute;left:48px;top:1475px;width:1101px;height:462px;display:grid;grid-template-columns:repeat(4,1fr);grid-template-rows:repeat(2,1fr)}
.act-photo{background:linear-gradient(135deg,#c9a27c,#e5c46a 45%,#6c8fb7)}
.act-photo.b{background:linear-gradient(135deg,#a9a39a,#e6e1d6 50%,#7a6757)}
.act-photo.c{background:linear-gradient(135deg,#7e5a48,#c7a7c9 50%,#d7684f)}
.act-photo.d{background:linear-gradient(135deg,#9c8f6a,#f0c73b 55%,#b6392c)}
.act-card{background:var(--blue);padding:38px 22px 0 26px;color:var(--white)}
.act-card h3{font-family:"Merriweather",serif;font-size:16.5px;font-weight:700;margin-bottom:18px}
.act-card p{font-size:14px;line-height:22px;color:var(--blue-soft)}
.act-meta{display:flex;align-items:center;font-size:12.5px;margin-top:18px;gap:8px}

/* parents banner */
.parents{position:absolute;left:0;top:1990px;width:1200px;height:244px;background:linear-gradient(90deg,var(--blue-deep),var(--blue) 55%,var(--blue))}
.parents-photo{position:absolute;left:0;top:0;width:600px;height:244px;background:linear-gradient(90deg,rgba(255,255,255,.08),rgba(255,255,255,0))}
.parents h2{position:absolute;left:87px;top:78px;font-family:"Merriweather",serif;font-weight:700;font-size:38px;color:var(--white)}
.parents p{position:absolute;left:87px;top:142px;width:440px;font-size:17px;line-height:22px;color:var(--white)}
.parents-person{position:absolute;left:709px;top:2000px;width:430px;height:170px;background:linear-gradient(180deg,#4a3026,#b78467 55%,#2b2f3a)}
.parents-box{position:absolute;left:749px;top:2149px;width:389px;height:74px;background:var(--white);display:flex;align-items:center;justify-content:center;font-family:"Merriweather",serif;font-weight:700;font-size:22px;letter-spacing:.5px}

/* contact */
.map{position:absolute;left:0;top:2637px;width:1200px;height:385px;background:linear-gradient(160deg,#efece6,#e6e9e4 50%,#ece7dc)}
.enquiry{position:absolute;left:236px;top:2357px;width:356px;height:328px;background:var(--white);box-shadow:0 0 6px rgba(0,0,0,.15)}
.enquiry h2{position:absolute;top:20px;width:100%;text-align:center;font-family:"Merriweather",serif;font-size:22px;color:var(--blue);letter-spacing:1px}
.field{position:absolute;left:32px;width:291px;height:37px;border:1.5px solid #8a8fa0;border-radius:6px;display:flex;align-items:center;gap:8px;padding-left:10px;font-size:12px;color:#888}
.btn-submit{position:absolute;left:32px;top:283px;width:134px;height:30px;border-radius:8px;background:linear-gradient(180deg,#5a98cf,var(--blue));color:var(--white);font-weight:700;font-size:14px;display:flex;align-items:center;justify-content:center}
.contact-us{position:absolute;left:592px;top:2357px;width:355px;height:328px;background:var(--blue);color:var(--white)}
.contact-us h2{position:absolute;left:105px;top:20px;font-family:"Merriweather",serif;font-size:22px;letter-spacing:1px}
.c-icon{position:absolute;left:63px}
.c-label{position:absolute;left:105px;font-weight:700;font-size:13px}
.c-text{position:absolute;left:105px;font-size:16px;line-height:19px}

/* footer */
.site-footer{position:absolute;left:0;top:3022px;width:1200px;height:102px;background:var(--blue);color:var(--white)}
.site-footer .copy{position:absolute;left:35px;top:42px;font-size:13px}
.social{position:absolute;top:28px;width:46px;height:46px;border:2px solid var(--white);border-radius:50%}
</style>
</head>
<body>

<header class="site-header">
  <div class="brand"><span class="brand-dot"></span><span class="brand-name">Lycée Royal de Velmont</span></div>
  <nav class="nav">
    <svg class="home-icon" width="28" height="26" viewBox="0 0 28 26" fill="none" stroke="#0f67ad" stroke-width="1.6"><path d="M3 12 14 3l11 9"/><path d="M6 10v13h16V10"/><path d="M10 16a5 5 0 0 1 8 0M12 19a2 2 0 0 1 4 0"/></svg>
    <a class="active" style="left:478px">Home</a>
    <a style="left:592px">Kindergarten Primary</a>
    <a style="left:813px">Contact us</a>
    <a style="left:964px">Plan</a>
  </nav>
  <div class="btn-parents">Parents Area</div>
</header>

<section class="hero" role="img" aria-label="Classroom photo of a smiling boy raising his hand with classmates behind him">
  <div class="hero-shade"></div>
  <svg class="hero-arrow" style="left:36px" width="26" height="46" viewBox="0 0 26 46"><path d="M23 3 3 23l20 20" fill="none" stroke="#fff" stroke-width="3"/></svg>
  <svg class="hero-arrow" style="left:1140px" width="26" height="46" viewBox="0 0 26 46"><path d="M3 3l20 20L3 43" fill="none" stroke="#fff" stroke-width="3"/></svg>
  <div class="hero-eyebrow">PRIMARY SCHOOL</div>
  <div class="hero-school">Lycee Royal de Velmont</div>
  <div class="hero-title">BEST GIFT FOR A CHILD<br>IS A GREAT EDUCATION</div>
  <div class="btn-enroll">Enroll Now</div>
</section>

<section class="info-bar">
  <div class="info-icon" style="left:107px"><svg width="28" height="30" viewBox="0 0 28 30" fill="none" stroke="#0f67ad" stroke-width="2.4"><circle cx="14" cy="10" r="6"/><path d="M14 16v6M4 22c0 4 20 4 20 0"/></svg></div>
  <div class="info-label" style="left:196px">LOCATION</div>
  <div class="info-text" style="left:196px">Rue des Tilleuls 14, 4520<br>Velmont, Belgique</div>
  <div class="info-icon" style="left:466px"><svg width="32" height="32" viewBox="0 0 32 32" fill="none" stroke="#0f67ad" stroke-width="2.4"><circle cx="16" cy="16" r="13"/><path d="M16 8v8l5 4"/></svg></div>
  <div class="info-label" style="left:556px">TIMMING</div>
  <div class="info-text" style="left:556px;line-height:22px;top:46px">Du lundi au Vendredi<br>7h00 - 18h</div>
  <div class="info-icon" style="left:820px"><svg width="28" height="28" viewBox="0 0 28 28" fill="#0f67ad"><path d="M6 3l4 5-2 3c1 4 4 7 8 9l3-2 5 4-3 4C12 25 3 16 3 6z"/><path d="M17 5a7 7 0 0 1 6 6M17 9a3 3 0 0 1 2 2" stroke="#0f67ad" stroke-width="1.8" fill="none"/></svg></div>
  <div class="info-label" style="left:910px">PHONE NUMBER</div>
  <div class="info-text" style="left:910px">+32 81 40 55 17</div>
</section>

<h2 class="section-title" style="top:790px">BLOG</h2>

<article class="card" style="left:36px;width:340px">
  <div class="card-head"><span>News</span></div>
  <div class="post" style="top:70px"><div class="thumb" role="img" aria-label="Photo of pupils at their desks"></div><div class="date">Oct<br>21</div><div class="post-text">Lorem Ipsum has been the industry's standard.<div class="meta"><svg width="20" height="20" viewBox="0 0 20 20" fill="none" stroke="#222" stroke-width="1.5"><circle cx="10" cy="10" r="8.5"/><path d="M10 5v5l3 2"/></svg>11-00pm&nbsp; 12-mon-19</div></div></div>
  <div class="post" style="top:190px"><div class="thumb" role="img" aria-label="Photo of a pupil drawing"></div><div class="date">Oct<br>21</div><div class="post-text">Lorem Ipsum has been the industry's standard.<div class="meta"><svg width="20" height="20" viewBox="0 0 20 20" fill="none" stroke="#222" stroke-width="1.5"><circle cx="10" cy="10" r="8.5"/><path d="M10 5v5l3 2"/></svg>11-00pm&nbsp; 12-mon-19</div></div></div>
  <div class="post" style="top:310px"><div class="thumb" role="img" aria-label="Photo of a teacher with a pupil"></div><div class="date">Oct<br>21</div><div class="post-text">Lorem Ipsum has been the industry's standard.<div class="meta"><svg width="20" height="20" viewBox="0 0 20 20" fill="none" stroke="#222" stroke-width="1.5"><circle cx="10" cy="10" r="8.5"/><path d="M10 5v5l3 2"/></svg>11-00pm&nbsp; 12-mon-19</div></div></div>
  <div class="btn-view">View ALL</div>
</article>

<article class="card" style="left:436px;width:329px">
  <div class="card-head"><span>Notice Board</span></div>
  <div class="notice" style="top:53px;height:113px"><p>Lorem Ipsum has been the industry's standard dummy text.</p><div class="meta"><svg width="20" height="20" viewBox="0 0 20 20" fill="none" stroke="#222" stroke-width="1.5"><circle cx="10" cy="10" r="8.5"/><path d="M10 5v5l3 2"/></svg>11-00pm&nbsp; 12-mon-19</div></div>
  <div class="notice" style="top:166px;height:115px"><p>Lorem Ipsum has been the industry's standard dummy text.</p><div class="meta"><svg width="20" height="20" viewBox="0 0 20 20" fill="none" stroke="#222" stroke-width="1.5"><circle cx="10" cy="10" r="8.5"/><path d="M10 5v5l3 2"/></svg>11-00pm&nbsp; 12-mon-19</div></div>
  <div class="notice" style="top:281px;height:116px"><p>Lorem Ipsum has been the industry's standard dummy text.</p><div class="meta"><svg width="20" height="20" viewBox="0 0 20 20" fill="none" stroke="#222" stroke-width="1.5"><circle cx="10" cy="10" r="8.5"/><path d="M10 5v5l3 2"/></svg>11-00pm&nbsp; 12-mon-19</div></div>
  <div class="btn-view">View ALL</div>
</article>

<article class="card" style="left:828px;width:337px">
  <div class="card-head"><span>Latest News</span></div>
  <div class="post" style="top:68px"><div class="thumb" role="img" aria-label="Photo of pupils at their desks"></div><div class="date">Oct<br>21</div><div class="post-text">Lorem Ipsum has been the industry's standard.<div class="meta"><svg width="20" height="20" viewBox="0 0 20 20" fill="none" stroke="#222" stroke-width="1.5"><circle cx="10" cy="10" r="8.5"/><path d="M10 5v5l3 2"/></svg>11-00pm&nbsp; 12-mon-19</div></div></div>
  <div class="post" style="top:188px"><div class="thumb" role="img" aria-label="Photo of pupils at their desks"></div><div class="date">Oct<br>21</div><div class="post-text">Lorem Ipsum has been the industry's standard.<div class="meta"><svg width="20" height="20" viewBox="0 0 20 20" fill="none" stroke="#222" stroke-width="1.5"><circle cx="10" cy="10" r="8.5"/><path d="M10 5v5l3 2"/></svg>11-00pm&nbsp; 12-mon-19</div></div></div>
  <div class="post" style="top:308px"><div class="thumb" role="img" aria-label="Photo of pupils at their desks"></div><div class="date">Oct<br>21</div><div class="post-text">Lorem Ipsum has been the industry's standard.<div class="meta"><svg width="20" height="20" viewBox="0 0 20 20" fill="none" stroke="#222" stroke-width="1.5"><circle cx="10" cy="10" r="8.5"/><path d="M10 5v5l3 2"/></svg>11-00pm&nbsp; 12-mon-19</div></div></div>
  <div class="btn-view">View ALL</div>
</article>

<h2 class="section-title" style="top:1403px">ACTIVITIES</h2>

<section class="activities">
  <div class="act-photo" role="img" aria-label="Photo of a teacher painting with young children"></div>
  <div class="act-card"><h3>Lorem Ipsum has been</h3><p>Lorem Ipsum has been the industry's standard dummy text ever since the 1500s.</p><div class="act-meta"><svg width="20" height="18" viewBox="0 0 20 18" fill="#fff"><path d="M2 2h16v11H8l-4 4v-4H2z"/></svg>10 comments<svg style="margin-left:22px" width="22" height="14" viewBox="0 0 22 14"><path d="M1 7c5-8 15-8 20 0-5 8-15 8-20 0z" fill="#fff"/><circle cx="11" cy="7" r="3" fill="#0f67ad"/></svg><span style="margin-left:14px">10 Views</span></div></div>
  <div class="act-photo b" role="img" aria-label="Photo of a classroom with pupils raising their hands"></div>
  <div class="act-card" style="padding-top:30px"><h3>Lorem Ipsum has been</h3><p>Lorem Ipsum has been the industry's standard dummy text ever since the 1500s.</p><div class="act-meta"><svg width="20" height="18" viewBox="0 0 20 18" fill="#fff"><path d="M2 2h16v11H8l-4 4v-4H2z"/></svg>10 comments<svg style="margin-left:22px" width="22" height="14" viewBox="0 0 22 14"><path d="M1 7c5-8 15-8 20 0-5 8-15 8-20 0z" fill="#fff"/><circle cx="11" cy="7" r="3" fill="#0f67ad"/></svg><span style="margin-left:14px">10 Views</span></div></div>
  <div class="act-card" style="padding-top:34px"><h3>Lorem Ipsum has been</h3><p>Lorem Ipsum has been the industry's standard dummy text ever since the 1500s.</p><div class="act-meta"><svg width="20" height="18" viewBox="0 0 20 18" fill="#fff"><path d="M2 2h16v11H8l-4 4v-4H2z"/></svg>10 comments<svg style="margin-left:22px" width="22" height="14" viewBox="0 0 22 14"><path d="M1 7c5-8 15-8 20 0-5 8-15 8-20 0z" fill="#fff"/><circle cx="11" cy="7" r="3" fill="#0f67ad"/></svg><span style="margin-left:14px">10 Views</span></div></div>
  <div class="act-photo c" role="img" aria-label="Photo of children showing their drawings"></div>
  <div class="act-card" style="padding-top:36px"><h3>Lorem Ipsum has been</h3><p>Lorem Ipsum has been the industry's standard dummy text ever since the 1500s.</p><div class="act-meta"><svg width="20" height="18" viewBox="0 0 20 18" fill="#fff"><path d="M2 2h16v11H8l-4 4v-4H2z"/></svg>10 comments<svg style="margin-left:22px" width="22" height="14" viewBox="0 0 22 14"><path d="M1 7c5-8 15-8 20 0-5 8-15 8-20 0z" fill="#fff"/><circle cx="11" cy="7" r="3" fill="#0f67ad"/></svg><span style="margin-left:14px">10 Views</span></div></div>
  <div class="act-photo d" role="img" aria-label="Photo of children around a yellow craft table"></div>
</section>

<section class="parents">
  <div class="parents-photo" role="img" aria-label="Faded photo of a parent and child"></div>
  <h2>Special for parents area</h2>
  <p>Lorem Ipsum has been the industry's standard dummy text ever since the 1500s</p>
</section>
<div class="parents-person" role="img" aria-label="Photo of a smiling woman pointing at the sign"></div>
<div class="parents-box">Parents Area</div>

<h2 class="section-title" style="top:2286px">CONTACT FORM</h2>

<div class="map" role="img" aria-label="Road map of the region around the school with a location pin"></div>

<form class="enquiry">
  <h2>QUICK ENQUIRY</h2>
  <div class="field" style="top:67px"><svg width="14" height="14" viewBox="0 0 14 14" fill="#0f67ad"><circle cx="7" cy="4" r="3.5"/><path d="M1 14c0-5 12-5 12 0z"/></svg>First name</div>
  <div class="field" style="top:120px"><svg width="14" height="14" viewBox="0 0 14 14" fill="#0f67ad"><path d="M3 1l3 3-1.5 2c1 2 2 3 3.5 3.5L10 8l3 3-2 2C6 13 1 8 1 3z"/></svg>Phone number</div>
  <div class="field" style="top:174px"><svg width="16" height="12" viewBox="0 0 16 12" fill="#0f67ad"><rect width="16" height="12" rx="1"/><path d="M1 1l7 6 7-6" stroke="#fff" fill="none"/></svg>Mail</div>
  <div class="field" style="top:227px"><svg width="16" height="12" viewBox="0 0 16 12" fill="#0f67ad"><rect width="16" height="12" rx="1"/><path d="M1 1l7 6 7-6" stroke="#fff" fill="none"/></svg>Message</div>
  <div class="btn-submit">Submit</div>
</form>

<section class="contact-us">
  <h2>CONTACT US</h2>
  <svg class="c-icon" style="top:67px" width="18" height="20" viewBox="0 0 18 20" fill="none" stroke="#fff" stroke-width="2"><circle cx="9" cy="7" r="4"/><path d="M9 11v4M2 15c0 3 14 3 14 0"/></svg>
  <div class="c-label" style="top:70px">LOCATION</div>
  <div class="c-text" style="top:97px">Rue des Tilleuls 14, 4520<br>Velmont, Belgique</div>
  <svg class="c-icon" style="top:153px" width="20" height="20" viewBox="0 0 20 20" fill="none" stroke="#fff" stroke-width="2"><circle cx="10" cy="10" r="8"/><path d="M10 5v5l3 2"/></svg>
  <div class="c-label" style="top:154px">TIMMING</div>
  <div class="c-text" style="top:181px;line-height:22px">Du lundi au Vendredi<br>7h00 - 18h</div>
  <svg class="c-icon" style="top:246px" width="18" height="22" viewBox="0 0 18 22" fill="#fff"><path d="M4 1l4 5-2 3c1 3 3 6 6 7l2-2 4 4-3 3C7 20 1 11 1 4z"/></svg>
  <div class="c-label" style="top:250px">PHONE NUMBER</div>
  <div class="c-text" style="top:277px">+32 81 40 55 17</div>
</section>

<footer class="site-footer">
  <div class="copy">Copyrights © 2019&nbsp; School . All Rights reserved.</div>
  <div class="social" style="left:994px" aria-label="Social profile"></div>
  <div class="social" style="left:1056px" aria-label="Social profile"></div>
  <div class="social" style="left:1118px" aria-label="Social profile"></div>
</footer>

</body>
</html>
```